Business card design Needed for new logo / Construction business, home extensions and new builds

We need a business card design using our new logo files which i will attach to this project :)

We are a small construction business specialising in home extensions, new builds and property development. We are very ambitious and would appreciate professional and elegant designs for our new business card.

Very serious about using the services on MakerQuarry and recently acquired our new logo from here :)

Please get involved, i will feedback when i can as i am very busy but can respond daily, thanks

Target Market(s)

People that want to build onto their houses, new building developments or adding too their existing property

Industry/Entity Type

Construction

Contact Information for Business Card

Renwick Tolliver Construction, Lionel Ashby (Managing Director), Tel 07822254961, email - info@renwick-tolliver, www.renwick-tolliver.co.uk

Colors

Designer to choose colors to be used in the design.

Requirements
Must have
• I like a deep grey on the back please. A lot of you have provided black from and back, try mixing things up a little. The black looks cool 😎 Thanks

```html
<!DOCTYPE html>
<html lang="en">
<head>
<meta charset="utf-8">
<title>Renwick Tolliver Construction – Business Card</title>
<link rel="stylesheet" href="https://fonts.googleapis.com/css2?family=Open+Sans:wght@400;600;700&display=swap">
<style>
  :root {
    --canvas: #2b2d33;
    --card-black: #1e1d22;
    --card-back: #18181b;
    --gold-deep: #c98a1f;
    --gold-mid: #e6b04a;
    --gold-light: #f7d98a;
    --silver: #c9cbcf;
    --silver-dark: #8d9096;
    --white: #f4f4f4;
    --emboss: #2c2c31;
  }
  * { box-sizing: border-box; margin: 0; padding: 0; }
  html, body {
    width: 1200px; height: 780px; overflow: hidden;
    background: var(--canvas);
    font-family: "Open Sans", Arial, sans-serif;
  }
  .canvas {
    width: 1200px; height: 780px;
    display: flex; align-items: center; justify-content: center; gap: 40px;
  }
  .card {
    position: relative;
    width: 540px; height: 309px;
    border-radius: 3px;
    overflow: hidden;
    box-shadow: 0 14px 30px rgba(0,0,0,.45);
  }
  .card-front { background: var(--card-black); }
  .card-back {
    background: var(--card-back);
    display: flex; align-items: center; justify-content: center;
  }
  .front-shapes { position: absolute; inset: 0; }

  .person { position: absolute; left: 44px; top: 68px; }
  .person-name { font-size: 30px; font-weight: 700; line-height: 1; letter-spacing: .2px; }
  .person-name .first { color: var(--silver); }
  .person-name .last { color: var(--gold-mid); }
  .person-role { color: var(--white); font-size: 13px; margin-top: 6px; margin-left: 40px; letter-spacing: .3px; }

  .brand {
    position: absolute; right: 36px; top: 48px;
    display: flex; align-items: center; gap: 8px;
  }
  .brand-mark { width: 12px; height: 12px; background: var(--gold-mid); }
  .brand-name {
    color: var(--gold-mid); font-size: 15px; font-weight: 600;
    letter-spacing: 1.5px; text-transform: uppercase; line-height: 1.25; text-align: left;
  }

  .divider {
    position: absolute; left: 256px; top: 150px;
    width: 2px; height: 62px; background: var(--white);
    transform: rotate(12deg);
  }
  .contacts {
    position: absolute; left: 286px; top: 146px;
    list-style: none; color: var(--white); font-size: 13.5px; line-height: 23px;
  }
  .contacts li { display: flex; align-items: center; gap: 8px; }
  .contacts svg { width: 13px; height: 13px; flex: none; }

  .address {
    position: absolute; left: 30px; bottom: 30px;
    color: var(--white); font-size: 14px; letter-spacing: .3px;
    transform: rotate(4deg); transform-origin: left center;
  }

  .back-name {
    color: var(--emboss); font-size: 26px; font-weight: 700;
    letter-spacing: 3px; text-transform: uppercase; text-align: center; line-height: 1.3;
  }
</style>
</head>
<body>
<main class="canvas">
  <section class="card card-front" aria-label="Business card front">
    <svg class="front-shapes" viewBox="0 0 540 309" preserveAspectRatio="none" aria-hidden="true">
      <defs>
        <linearGradient id="goldBand" x1="0" y1="0" x2="1" y2="0.4">
          <stop offset="0" stop-color="#d4962a"/>
          <stop offset=".22" stop-color="#f7d98a"/>
          <stop offset=".45" stop-color="#c98a1f"/>
          <stop offset=".7" stop-color="#f2cf7c"/>
          <stop offset="1" stop-color="#d29a33"/>
        </linearGradient>
        <linearGradient id="silverLine" x1="0" y1="0" x2="1" y2="0">
          <stop offset="0" stop-color="#8d9096"/>
          <stop offset=".5" stop-color="#e4e6ea"/>
          <stop offset="1" stop-color="#9a9da3"/>
        </linearGradient>
      </defs>
      <path class="gold-band" d="M0 212 C 70 195, 120 240, 250 268 C 360 290, 460 298, 540 300 L540 309 L0 309 Z" fill="url(#goldBand)"/>
      <path class="silver-curve" d="M0 198 C 60 185, 110 226, 240 256 C 350 280, 450 290, 540 292" fill="none" stroke="url(#silverLine)" stroke-width="3"/>
    </svg>

    <div class="person">
      <h1 class="person-name"><span class="first">Lionel</span> <span class="last">Ashby</span></h1>
      <p class="person-role">Managing Director</p>
    </div>

    <div class="brand">
      <span class="brand-mark"></span>
      <span class="brand-name">Renwick Tolliver<br>Construction</span>
    </div>

    <span class="divider"></span>

    <ul class="contacts">
      <li>
        <svg viewBox="0 0 24 24" aria-hidden="true"><path fill="#e6b04a" d="M6.6 10.8a15 15 0 0 0 6.6 6.6l2.2-2.2c.3-.3.7-.4 1-.2 1.1.4 2.3.6 3.6.6.6 0 1 .4 1 1V20c0 .6-.4 1-1 1A17 17 0 0 1 3 4c0-.6.4-1 1-1h3.5c.6 0 1 .4 1 1 0 1.3.2 2.5.6 3.6.1.3 0 .7-.2 1z"/></svg>
        0782 225 4961
      </li>
      <li>
        <svg viewBox="0 0 24 24" aria-hidden="true"><rect x="2" y="5" width="20" height="14" rx="2" fill="#e6b04a"/><path d="M3 6l9 7 9-7" fill="none" stroke="#1e1d22" stroke-width="1.8"/></svg>
        info@renwick-tolliver.co.uk
      </li>
      <li>
        <svg viewBox="0 0 24 24" aria-hidden="true"><circle cx="12" cy="12" r="10" fill="#e6b04a"/><path d="M2 12h20M12 2c3 3 3 17 0 20M12 2c-3 3-3 17 0 20" fill="none" stroke="#1e1d22" stroke-width="1.4"/></svg>
        www.renwick-tolliver.co.uk
      </li>
    </ul>

    <p class="address">Halden Road, Westmoor Bournemouth, BH7 4QL</p>
  </section>

  <section class="card card-back" aria-label="Business card back">
    <p class="back-name">Renwick Tolliver<br>Construction</p>
  </section>
</main>
</body>
</html>
```